Irrigation Business needs their business cards modernised and revamped

I would like to keep my current logo, colours and revamp the format of the card.

I would like the card to be clean yet important.

Im not sure if you include texture but i would like the named logo to be indented into the card etc.

show me something alive and free something thats clinical to the point yet has a feel of achievement. i would like people to go nice card.

Target Market(s)

high end clients, corporate, sports field manger, the guys that make the decisions

Industry/Entity Type

Business

Contact Information for Business Card

nformation to be included

Dean Harlow (Director)
0487305526
dean@kolvat.biz
www.kestonfieldworks.com

instagram logo
google logo
facebook logo

Colors

Designer to choose colors to be used in the design.

Requirements
Nice to have
• indentations a really nice feel to the card good texture

```html
<!DOCTYPE html>
<html lang="en">
<head>
<meta charset="utf-8">
<title>Keston Fieldworks – Business Cards</title>
<link rel="stylesheet" href="https://fonts.googleapis.com/css2?family=Arimo:wght@400;700&display=swap">
<style>
  :root {
    --backdrop: #2b2b2d;
    --card: #f7f7f7;
    --blue: #2e64aa;
    --blue-dark: #1f4f99;
    --green: #23924a;
    --white: #ffffff;
    --ink: #14233f;
  }
  * { box-sizing: border-box; margin: 0; padding: 0; }
  html, body {
    width: 1200px; height: 997px; overflow: hidden;
    background: var(--backdrop);
    font-family: "Arimo", Arial, sans-serif;
  }
  .stage { position: relative; width: 1200px; height: 997px; }
  .card {
    position: absolute; left: 320px; width: 560px; height: 320px;
    background: var(--card); border-radius: 14px; overflow: hidden;
  }
  .card--front { top: 140px; }
  .card--back { top: 520px; }

  .brand {
    position: absolute; left: 0; right: 0;
    display: flex; align-items: center; justify-content: center; gap: 12px;
  }
  .brand__dot {
    width: 44px; height: 44px; border-radius: 50%; background: var(--blue);
  }
  .brand__name {
    font-weight: 700; font-size: 30px; letter-spacing: 0.5px; color: var(--blue-dark);
  }
  .card--front .brand { top: 110px; }
  .card--back .brand { top: 52px; }

  .rule { position: absolute; left: 0; right: 0; height: 2px; background: var(--blue); }

  .service-band {
    position: absolute; left: 0; right: 0; top: 232px; height: 40px; display: flex;
  }
  .service-band__item {
    flex: 1; display: flex; align-items: center; justify-content: center;
    color: var(--white); font-size: 15px; letter-spacing: 1px;
  }
  .service-band__item--residential { background: var(--blue); }
  .service-band__item--commercial { background: var(--green); }

  .contact-band {
    position: absolute; left: 0; right: 0; top: 146px; height: 104px; display: flex;
  }
  .contact-band__person {
    width: 50%; background: var(--blue); padding: 40px 0 0 46px;
  }
  .person__name { color: var(--white); font-weight: 700; font-size: 19px; letter-spacing: 0.5px; }
  .person__role { color: var(--ink); font-weight: 700; font-size: 15px; margin-top: 2px; padding-left: 26px; }
  .contact-band__details {
    width: 50%; background: var(--green); padding: 22px 0 0 60px;
    display: flex; flex-direction: column; gap: 10px;
  }
  .detail { display: flex; align-items: center; gap: 10px; color: var(--white); font-size: 15px; letter-spacing: 0.5px; }
  .detail__icon { width: 16px; height: 16px; flex: none; }

  .address {
    position: absolute; left: 0; right: 0; top: 272px; text-align: center;
    color: var(--blue-dark); font-weight: 700; font-size: 18px; letter-spacing: 1.5px;
  }
</style>
</head>
<body>
<main class="stage">

  <section class="card card--front" aria-label="Card front">
    <div class="brand">
      <span class="brand__dot"></span>
      <span class="brand__name">KESTON FIELDWORKS</span>
    </div>
    <div class="rule" style="top:224px"></div>
    <div class="service-band">
      <div class="service-band__item service-band__item--residential">RESIDENTIAL SERVICES</div>
      <div class="service-band__item service-band__item--commercial">COMMERCIAL SERVICES</div>
    </div>
    <div class="rule" style="top:278px"></div>
  </section>

  <section class="card card--back" aria-label="Card back">
    <div class="brand">
      <span class="brand__dot"></span>
      <span class="brand__name">KESTON FIELDWORKS</span>
    </div>
    <div class="rule" style="top:138px"></div>
    <div class="contact-band">
      <div class="contact-band__person">
        <p class="person__name">DEAN HARLOW</p>
        <p class="person__role">Director</p>
      </div>
      <div class="contact-band__details">
        <p class="detail">
          <svg class="detail__icon" viewBox="0 0 16 16" aria-hidden="true">
            <circle cx="8" cy="8" r="8" fill="#fff"/>
            <path d="M4 6.5c0-1.5 1.8-2 4-2s4 .5 4 2l-1.5.5-.5-1H6l-.5 1z M5.5 7.5h5l1 3.5h-7z" fill="#23924a"/>
          </svg>
          0487305526
        </p>
        <p class="detail">
          <svg class="detail__icon" viewBox="0 0 16 16" aria-hidden="true">
            <circle cx="8" cy="8" r="8" fill="#fff"/>
            <rect x="4" y="5" width="8" height="6" fill="#23924a"/>
            <path d="M4 5l4 3.5L12 5" stroke="#fff" stroke-width="1" fill="none"/>
          </svg>
          dean@kolvat.biz
        </p>
      </div>
    </div>
    <div class="rule" style="top:256px"></div>
    <p class="address">PO BOX 218 GLENMORE, B.C. QLD 4417</p>
  </section>

</main>
</body>
</html>
```